Reliable and clean label for a natural product!

We would like to have a label design for our CBD SOFT GEL CAPSULES . We are a business family and believe in the power of natural healing. In this label we would like to show a reliable, natural and feminine product mainly.

Font styles to use
Serif
Sans Serif

Colors

Designer to choose colors to be used in the design.

```html
<!DOCTYPE html>
<html lang="en">
<head>
<meta charset="utf-8">
<title>Verdalia CBD – Soft Gel Capsule Labels</title>
<link rel="stylesheet" href="https://fonts.googleapis.com/css2?family=Inter:wght@400&family=Oswald:wght@500&family=Questrial&family=Mrs+Saint+Delafield&display=swap">
<style>
  :root {
    --ink: #3b3b3b;
    --ink-soft: #4a4a4a;
    --paper: #ffffff;
    --sage-dark: #a9c4b4; --sage-light: #e3eee7; --sage-accent: #98b9a8;
    --sky-dark: #8fbccf;  --sky-light: #d4e9f2;  --sky-accent: #89bfd2;
    --lilac-dark: #b8a5c6; --lilac-light: #e6dcec; --lilac-accent: #b49cc4;
    --honey-dark: #e6c38f; --honey-light: #f6e4c6; --honey-accent: #e2ab6d;
    --blush-dark: #dcc6b9; --blush-light: #f4e9e2; --blush-accent: #e4b5a6;
  }
  * { box-sizing: border-box; margin: 0; padding: 0; }
  html, body { width: 1200px; height: 1200px; overflow: hidden; background: var(--paper); }
  .canvas { position: relative; width: 1200px; height: 1200px; background: var(--paper); }

  .label {
    position: absolute; top: 351px; width: 206px; height: 243px;
    background: var(--paper);
    box-shadow: inset 0 0 0 1px rgba(0,0,0,0.04);
    text-align: center; color: var(--ink);
    overflow: hidden;
  }
  .label--sage  { left: 37px;  --band-dark: var(--sage-dark);  --band-light: var(--sage-light);  --accent: var(--sage-accent); }
  .label--sky   { left: 267px; --band-dark: var(--sky-dark);   --band-light: var(--sky-light);   --accent: var(--sky-accent); }
  .label--lilac { left: 497px; --band-dark: var(--lilac-dark); --band-light: var(--lilac-light); --accent: var(--lilac-accent); }
  .label--honey { left: 727px; --band-dark: var(--honey-dark); --band-light: var(--honey-light); --accent: var(--honey-accent); }
  .label--blush { left: 957px; --band-dark: var(--blush-dark); --band-light: var(--blush-light); --accent: var(--blush-accent); }

  .label__band {
    position: absolute; left: 0; right: 0; top: 90px; bottom: 0;
    background: linear-gradient(100deg, var(--band-light) 0%, var(--band-dark) 55%, var(--band-light) 100%);
  }
  .label__tagline {
    position: absolute; left: 0; right: 0; top: 10px;
    font: 400 7.5px/1 "Inter", sans-serif; letter-spacing: 0.2px;
    color: var(--accent); text-transform: uppercase;
  }
  .label__brand {
    position: absolute; left: 0; right: 0; top: 38px;
    font: 400 14.5px/1 "Inter", sans-serif; letter-spacing: 0.3px; color: var(--ink-soft);
  }
  .label__seal {
    position: absolute; left: 78px; top: 61px; width: 50px; height: 50px;
    border-radius: 50%; background: var(--paper);
    border: 1.5px solid var(--accent);
  }
  .label__product {
    position: absolute; left: 0; right: 0; top: 119px;
    font: 500 22px/1 "Oswald", sans-serif; letter-spacing: 0.5px; color: var(--ink-soft);
  }
  .label__format {
    position: absolute; left: 0; right: 0; top: 143px;
    font: 400 30px/1 "Mrs Saint Delafield", cursive; color: var(--ink);
  }
  .label__spectrum {
    position: absolute; left: 54px; top: 178px; width: 99px; height: 16px;
    border: 1px solid rgba(255,255,255,0.9);
    font: 400 10px/14px "Questrial", sans-serif; letter-spacing: 0.6px; color: var(--ink);
  }
  .label__dose {
    position: absolute; left: 0; right: 0; top: 203px;
    font: 400 10px/1 "Questrial", sans-serif; letter-spacing: 0.4px; color: var(--ink);
  }
  .label__rule {
    position: absolute; left: 66px; top: 219px; width: 74px; height: 1px;
    background: linear-gradient(90deg, transparent, var(--ink) 50%, transparent);
  }
  .label__count {
    position: absolute; left: 0; right: 0; top: 227px;
    font: 400 9.5px/1 "Questrial", sans-serif; letter-spacing: 0.8px; color: var(--ink);
  }
</style>
</head>
<body>
<main class="canvas">
  <article class="label label--sage">
    <div class="label__band"></div>
    <p class="label__tagline">Restorative Supplement</p>
    <h2 class="label__brand">VERDALIA CBD</h2>
    <div class="label__seal"></div>
    <h1 class="label__product">CBD SOFT GELS</h1>
    <p class="label__format">Capsules</p>
    <p class="label__spectrum">FULL SPECTRUM</p>
    <p class="label__dose">25mg cbd per capsule</p>
    <div class="label__rule"></div>
    <p class="label__count">30 CAPSULES</p>
  </article>

  <article class="label label--sky">
    <div class="label__band"></div>
    <p class="label__tagline">Restorative Supplement</p>
    <h2 class="label__brand">VERDALIA CBD</h2>
    <div class="label__seal"></div>
    <h1 class="label__product">CBD SOFT GELS</h1>
    <p class="label__format">Capsules</p>
    <p class="label__spectrum">FULL SPECTRUM</p>
    <p class="label__dose">25mg cbd per capsule</p>
    <div class="label__rule"></div>
    <p class="label__count">30 CAPSULES</p>
  </article>

  <article class="label label--lilac">
    <div class="label__band"></div>
    <p class="label__tagline">Restorative Supplement</p>
    <h2 class="label__brand">VERDALIA CBD</h2>
    <div class="label__seal"></div>
    <h1 class="label__product">CBD SOFT GELS</h1>
    <p class="label__format">Capsules</p>
    <p class="label__spectrum">FULL SPECTRUM</p>
    <p class="label__dose">25mg cbd per capsule</p>
    <div class="label__rule"></div>
    <p class="label__count">30 CAPSULES</p>
  </article>

  <article class="label label--honey">
    <div class="label__band"></div>
    <p class="label__tagline">Restorative Supplement</p>
    <h2 class="label__brand">VERDALIA CBD</h2>
    <div class="label__seal"></div>
    <h1 class="label__product">CBD SOFT GELS</h1>
    <p class="label__format">Capsules</p>
    <p class="label__spectrum">FULL SPECTRUM</p>
    <p class="label__dose">25mg cbd per capsule</p>
    <div class="label__rule"></div>
    <p class="label__count">30 CAPSULES</p>
  </article>

  <article class="label label--blush">
    <div class="label__band"></div>
    <p class="label__tagline">Restorative Supplement</p>
    <h2 class="label__brand">VERDALIA CBD</h2>
    <div class="label__seal"></div>
    <h1 class="label__product">CBD SOFT GELS</h1>
    <p class="label__format">Capsules</p>
    <p class="label__spectrum">FULL SPECTRUM</p>
    <p class="label__dose">25mg cbd per capsule</p>
    <div class="label__rule"></div>
    <p class="label__count">30 CAPSULES</p>
  </article>
</main>
</body>
</html>
```